Duct Manufacturing Company new to the industry needs business card and stationary design

we are sheet metal duct manufacturers looking for a business card design to fit my new business logo.
nothing to crazy that will date, but want it to stand out from the crowed.
I'm sure you guys will work it out.

Contact Information for Business Card

Glen Marsh
Director

Address
17 Dorwell St
Ashbridge NSW 2735

0438 760 514

Sales@flowbend.com.au

Font styles to use
Other font styles liked:
• BankGothic md bt

Requirements
Nice to have
• Like the idea of corner rounded to match logo
• like to keep colours flowing
• font I like sharp square not rounded

```html
<!DOCTYPE html>
<html lang="en">
<head>
<meta charset="utf-8">
<title>Flowbend Industries – Business Card</title>
<link rel="stylesheet" href="https://fonts.googleapis.com/css2?family=Michroma&display=swap">
<style>
  :root {
    --bg: #ecebe7;
    --card: #ffffff;
    --blue: #1b93d1;
    --blue-deep: #0c6aa8;
    --green: #9fcb3a;
    --ink: #1f2429;
    --grey: #8b8f93;
  }
  * { box-sizing: border-box; margin: 0; padding: 0; }
  html, body { width: 1200px; height: 780px; overflow: hidden; background: var(--bg); }
  body { font-family: "Michroma", sans-serif; color: var(--ink); position: relative; }

  .card {
    position: absolute;
    width: 540px; height: 310px;
    border-radius: 18px;
    background: var(--card);
    overflow: hidden;
    box-shadow: 0 6px 18px rgba(0,0,0,.15);
  }
  .card-front { left: 40px; top: 235px; }
  .card-back  { left: 620px; top: 235px; }
  .card-art { position: absolute; inset: 0; width: 100%; height: 100%; }

  /* front */
  .front-name {
    position: absolute; left: 0; right: 0; top: 118px;
    text-align: center; color: var(--green);
    text-transform: uppercase; line-height: 1.1;
  }
  .front-name .line-1 { display: block; font-size: 44px; letter-spacing: 1px; }
  .front-name .line-2 { display: block; font-size: 22px; letter-spacing: 7px; }

  /* back */
  .brand {
    position: absolute; left: 28px; top: 30px;
    display: flex; align-items: center; gap: 10px;
    color: var(--blue); text-transform: uppercase; font-size: 15px; line-height: 1.2;
  }
  .brand-dot { width: 30px; height: 30px; border-radius: 50%; background: var(--blue); flex: none; }
  .person { position: absolute; right: 28px; top: 34px; text-align: right; text-transform: uppercase; }
  .person-name { color: var(--blue); font-size: 17px; letter-spacing: 1.5px; }
  .person-role { font-size: 10px; letter-spacing: 1.5px; margin-top: 4px; }

  .contact { position: absolute; right: 28px; top: 128px; text-align: right; font-size: 10px; text-transform: uppercase; letter-spacing: 1px; }
  .contact-row { display: flex; justify-content: flex-end; align-items: center; gap: 8px; margin-bottom: 10px; }
  .contact-icon { width: 14px; height: 14px; }

  .address {
    position: absolute; left: 28px; bottom: 22px;
    font-size: 10px; letter-spacing: 1.5px; text-transform: uppercase; color: var(--ink); line-height: 1.7;
  }
</style>
</head>
<body>

<div class="card card-front">
  <svg class="card-art" viewBox="0 0 540 310" aria-hidden="true">
    <path d="M0 0 H540 V30 Q300 62 0 82 Z" fill="var(--blue)"/>
    <path d="M0 82 Q300 62 540 30 V44 Q300 84 0 98 Z" fill="var(--green)"/>
    <path d="M0 228 Q240 238 540 206 V222 Q240 254 0 244 Z" fill="var(--green)"/>
    <path d="M0 244 Q240 254 540 222 V310 H0 Z" fill="var(--blue)"/>
  </svg>
  <div class="front-name">
    <span class="line-1">Flowbend</span>
    <span class="line-2">Industries</span>
  </div>
</div>

<div class="card card-back">
  <svg class="card-art" viewBox="0 0 540 310" aria-hidden="true">
    <path d="M0 214 Q280 226 540 300 V310 H0 Z" fill="var(--green)"/>
    <path d="M0 226 Q280 240 540 310 H0 Z" fill="var(--blue)"/>
  </svg>

  <div class="brand">
    <span class="brand-dot"></span>
    <span>Flowbend<br>Industries</span>
  </div>

  <div class="person">
    <div class="person-name">Glen Marsh</div>
    <div class="person-role">Director</div>
  </div>

  <div class="contact">
    <div class="contact-row">
      <span>0438 760 514</span>
      <svg class="contact-icon" viewBox="0 0 14 14" aria-hidden="true">
        <rect width="14" height="14" rx="2" fill="var(--green)"/>
        <path d="M4 3 L6 3 L6.5 5.5 L5.5 6.5 Q6.5 8 7.5 8.5 L8.5 7.5 L11 8 L11 10 Q7 11 4 7 Q3 5 4 3 Z" fill="#fff"/>
      </svg>
    </div>
    <div class="contact-row">
      <span>Sales@flowbend.com.au</span>
      <svg class="contact-icon" viewBox="0 0 14 14" aria-hidden="true">
        <rect width="14" height="14" rx="2" fill="var(--green)"/>
        <rect x="3" y="4" width="8" height="6" fill="none" stroke="#fff" stroke-width="1"/>
        <path d="M3 4 L7 7.5 L11 4" fill="none" stroke="#fff" stroke-width="1"/>
      </svg>
    </div>
  </div>

  <div class="address">
    17 Dorwell St<br>
    Ashbridge NSW 2735
  </div>
</div>

</body>
</html>
```